Design a web site for my business - Brightline Coatings Co.

We are a family business that handles design, fabrication and installation of powder coated aluminum, stainless steel and glass products. Including handrails, privacy slat screens, electric gates and pool fencing. We are based in the Whitsundays in North Queensland and service an area from Airlie Beach to Townsville.

Target Market(s)

Domestic and commercial

Industry/Entity Type

fabrication - manufacturing

Coding

Coded - Design and coding required

Number of Pages Required

5+ page

Colors
0054AA
0677BA
7BADD7
CADEEF
E8F1F8

Requirements
Must have
• photo galleries, contact page, one page for privacy screens, balustrades, glass fencing, stainless steel handrail, powder coated aluminium handrails and pool fencing

```html
<!DOCTYPE html>
<html lang="en">
<head>
<meta charset="utf-8">
<title>Brightline Coatings Co — Precision Fabrication in the Whitsundays</title>
<link href="https://fonts.googleapis.com/css2?family=Inter:wght@400;500;600;700;800&display=swap" rel="stylesheet">
<style>
:root{
  --blue-900:#0054AA;
  --blue-700:#0677BA;
  --blue-400:#7BADD7;
  --blue-200:#CADEEF;
  --blue-100:#E8F1F8;
  --ink:#0f1e33;
  --muted:#4f5d70;
  --line:#CADEEF;
  --paper:#fbfdff;
  --white:#ffffff;
}
*{box-sizing:border-box;margin:0;padding:0}
html,body{width:1200px;height:4642px;overflow:hidden}
body{font-family:"Inter",Arial,sans-serif;color:var(--ink);background:var(--paper);position:relative}
.wrap{width:1078px;margin:0 auto;position:relative}
a{color:inherit;text-decoration:none}

/* nav */
.site-nav{height:75px;background:var(--white);border-bottom:1px solid var(--blue-100)}
.site-nav .wrap{display:flex;align-items:center;height:75px}
.brand{font-weight:700;font-size:21px;letter-spacing:-.2px;color:var(--blue-900)}
.nav-links{display:flex;gap:30px;margin-left:140px;font-size:14px;color:var(--muted)}
.nav-links .active{color:var(--blue-900);font-weight:600;border-bottom:2px solid var(--blue-900);padding-bottom:6px;margin-top:8px}
.nav-cta{margin-left:auto;background:var(--blue-900);color:#fff;font-weight:600;font-size:14px;padding:14px 24px;border-radius:3px}

/* hero */
.hero{height:815px;position:relative;background:linear-gradient(180deg,#6f93b0 0%,#9cbcd2 25%,#3f8fb4 45%,#5f8288 70%,#8f8d86 100%)}
.hero-shade{position:absolute;inset:0;background:linear-gradient(90deg,rgba(0,52,110,.6),rgba(0,52,110,.05) 65%)}
.hero-copy{position:absolute;left:61px;top:315px;color:#fff;width:600px}
.hero h1{font-size:46px;line-height:1.14;font-weight:700;letter-spacing:-.8px}
.hero p{font-size:15.5px;line-height:1.65;margin-top:22px;color:#eef4fa;width:500px}
.hero-actions{display:flex;gap:18px;margin-top:38px}
.btn-light{background:#fff;color:var(--blue-900);font-weight:600;font-size:14px;padding:18px 30px;border-radius:3px;display:flex;gap:10px;align-items:center}
.btn-ghost{border:1.5px solid rgba(255,255,255,.8);color:#fff;font-weight:600;font-size:14px;padding:17px 30px;border-radius:3px}

/* expertise */
.expertise{height:785px;padding-top:92px;background:var(--paper)}
.eyebrow{font-size:11px;font-weight:700;letter-spacing:1.6px;text-align:center;color:var(--blue-700)}
.section-title{font-size:30px;font-weight:600;letter-spacing:-.4px;color:var(--ink)}
.centered{text-align:center}
.expertise .section-title{margin-top:12px}
.cards{display:flex;gap:24px;margin-top:56px}
.card{width:252px;height:482px;background:#fff;border:1px solid var(--line);padding:8px}
.card-media{height:235px}
.card h3{font-size:22px;font-weight:600;margin:28px 15px 0}
.card p{font-size:13.5px;line-height:1.65;color:var(--muted);margin:12px 15px 0}
.card .more{display:block;font-size:13.5px;font-weight:700;margin:16px 15px 0;color:var(--blue-900)}
.m-rail{background:linear-gradient(135deg,#b3b6b8,#7f8488)}
.m-screen{background:linear-gradient(135deg,#4f6f3c,#2b2e30 60%,#6a6f66)}
.m-gate{background:linear-gradient(180deg,#c9d6de,#8a5e3c 45%,#a99f92)}
.m-pool{background:linear-gradient(180deg,#9cc7e3,#2f8fc4 55%,#dfe8ea)}

/* about */
.about{height:816px;background:var(--blue-100);padding-top:90px}
.about-copy{width:500px}
.about h2{font-size:30px;font-weight:600;line-height:1.27;letter-spacing:-.4px}
.about .lead{font-size:16px;line-height:1.65;color:var(--muted);margin-top:30px}
.features{display:grid;grid-template-columns:230px 230px;column-gap:40px;row-gap:34px;margin-top:44px}
.feat-icon{width:44px;height:44px;background:var(--blue-900);display:flex;align-items:center;justify-content:center}
.feat h4{font-size:14px;font-weight:700;margin-top:18px}
.feat p{font-size:13.5px;line-height:1.65;color:var(--muted);margin-top:12px}
.about-media{position:absolute;left:569px;top:0;width:509px;height:635px;background:linear-gradient(135deg,#5c6a78,#1f4f86 45%,#7b8898)}
.stat{position:absolute;left:548px;top:532px;width:190px;height:128px;background:#fff;padding:28px 30px}
.stat strong{font-size:42px;font-weight:700;display:block;line-height:1;color:var(--blue-900)}
.stat span{font-size:10.5px;letter-spacing:1.6px;font-weight:600;display:block;margin-top:16px}

/* gallery */
.recent{height:551px;padding-top:90px;background:var(--paper)}
.recent-head{display:flex;justify-content:space-between;align-items:flex-end}
.recent-head p{font-size:14px;color:var(--muted);margin-top:14px}
.view-all{font-size:14px;font-weight:700;border-bottom:2px solid var(--blue-900);padding-bottom:4px;display:flex;gap:8px;align-items:center;color:var(--blue-900)}
.gallery{display:flex;gap:22px;margin-top:44px}
.gallery div{width:345px;height:258px}
.g1{background:linear-gradient(180deg,#7fb2d6,#2f86b8 55%,#4d6f4a)}
.g2{background:linear-gradient(135deg,#e4e6e8,#9b9fa4 50%,#3c4046)}
.g3{background:linear-gradient(180deg,#dfe5ea,#c8c0b0 50%,#6f6a63)}

/* testimonials */
.reviews{height:442px;padding-top:80px;background:var(--paper)}
.quotes{display:flex;justify-content:space-between;margin-top:58px}
.quote{width:320px;position:relative;text-align:center}
.quote svg{position:absolute;left:0;top:-8px}
.quote p{font-size:18px;line-height:1.58;position:relative;padding:0 30px 0 46px}
.quote cite{display:block;font-style:normal;font-weight:700;font-size:14px;margin-top:24px;color:var(--blue-900)}

/* contact */
.contact{height:740px;background:var(--paper)}
.contact-box{background:var(--blue-100);height:600px;padding:60px;display:flex;justify-content:space-between}
.contact-copy{width:440px}
.contact h2{font-size:30px;font-weight:600;letter-spacing:-.4px}
.contact .lead{font-size:15.5px;line-height:1.65;color:var(--muted);margin-top:24px}
.contact-list{list-style:none;margin-top:26px}
.contact-list li{display:flex;align-items:center;gap:18px;font-size:14.5px;font-weight:600;margin-bottom:27px}
.ci{width:36px;height:36px;background:#fff;border-radius:50%;display:flex;align-items:center;justify-content:center}
.form{width:450px;height:476px;background:#fff;padding:34px 30px;box-shadow:0 1px 3px rgba(0,84,170,.08)}
.row{display:flex;gap:24px}
.field{flex:1;margin-bottom:26px}
.field label{display:block;font-size:10.5px;font-weight:700;letter-spacing:1.2px;margin-bottom:12px}
.input{border:1px solid var(--blue-200);height:44px;border-radius:2px;font-size:14px;color:#8a94a3;padding:12px 12px;display:flex;justify-content:space-between;align-items:center}
.input.sel{color:var(--ink)}
.input.area{height:112px;align-items:flex-start}
.submit{background:var(--blue-900);color:#fff;font-weight:600;font-size:14px;height:52px;display:flex;align-items:center;justify-content:center;border-radius:2px;margin-top:4px}

/* footer */
.footer{position:absolute;left:0;top:4224px;width:1200px;height:418px;background:var(--blue-900);color:#fff}
.footer-cols{display:flex;padding-top:60px}
.fcol{width:275px}
.f-brand{font-size:23px;font-weight:700;line-height:1.3;width:200px}
.f-tag{font-size:13.5px;line-height:1.6;color:var(--blue-200);margin-top:26px;width:230px}
.fcol h5{font-size:10.5px;letter-spacing:1.6px;font-weight:700}
.fcol ul{list-style:none;margin-top:26px}
.fcol li{font-size:14px;color:var(--blue-100);margin-bottom:18px}
.f-contact{font-size:14px;line-height:1.6;color:var(--blue-100);margin-top:24px;width:250px}
.f-btn{display:inline-block;background:#fff;color:var(--blue-900);font-weight:600;font-size:14px;padding:10px 22px;border-radius:2px;margin-top:16px}
.footer-bottom{position:absolute;left:61px;right:61px;top:330px;border-top:1px solid var(--blue-700);padding-top:28px;display:flex;justify-content:space-between;font-size:12px;color:var(--blue-200)}
.footer-bottom nav{display:flex;gap:30px}
</style>
</head>
<body>

<header class="site-nav">
  <div class="wrap">
    <div class="brand">Brightline Coatings Co</div>
    <nav class="nav-links">
      <a class="active" href="services.html">Services</a><a href="gallery.html">Projects</a><a href="areas.html">Areas</a><a href="about.html">About</a><a href="contact.html">Contact</a>
    </nav>
    <a class="nav-cta" href="contact.html">Request Quote</a>
  </div>
</header>

<section class="hero" role="img" aria-label="Modern coastal home with frameless glass balustrade overlooking an infinity pool and Whitsunday islands">
  <div class="hero-shade"></div>
  <div class="hero-copy">
    <h1>Precision Fabrication &amp; Professional Installation in the Whitsundays</h1>
    <p>Family-owned and operated, delivering premium aluminum, stainless steel, and glass solutions from Airlie Beach to Townsville.</p>
    <div class="hero-actions">
      <a class="btn-light" href="contact.html">Request a Free Quote <svg width="14" height="12" viewBox="0 0 14 12"><path d="M1 6h11M7 1l5 5-5 5" fill="none" stroke="#0054AA" stroke-width="1.6"/></svg></a>
      <a class="btn-ghost" href="gallery.html">View Recent Projects</a>
    </div>
  </div>
</section>

<section class="expertise">
  <div class="wrap">
    <div class="eyebrow">OUR EXPERTISE</div>
    <h2 class="section-title centered">High-End Solutions for Modern Living</h2>
    <div class="cards">
      <article class="card"><div class="card-media m-rail" role="img" aria-label="Stainless steel handrail on concrete wall"></div><h3>Handrails</h3><p>Durable stainless steel and aluminum handrails designed for safety and architectural elegance.</p><a class="more" href="handrails.html">Learn More →</a></article>
      <article class="card"><div class="card-media m-screen" role="img" aria-label="Black aluminium slat privacy screen on a balcony"></div><h3>Privacy Screens</h3><p>Elegant slat screening solutions that provide privacy without compromising on airflow or aesthetics.</p><a class="more" href="privacy-screens.html">Learn More →</a></article>
      <article class="card"><div class="card-media m-gate" role="img" aria-label="Timber-look electric sliding gate at a driveway"></div><h3>Electric Gates</h3><p>Secure and sophisticated automated gate systems custom-built for residential and commercial entries.</p><a class="more" href="electric-gates.html">Learn More →</a></article>
      <article class="card"><div class="card-media m-pool" role="img" aria-label="Frameless glass pool fence beside an ocean-view pool"></div><h3>Pool Fencing</h3><p>Frameless glass and aluminum pool fencing that meets all safety standards with a high-end finish.</p><a class="more" href="pool-fencing.html">Learn More →</a></article>
    </div>
  </div>
</section>

<section class="about">
  <div class="wrap">
    <div class="about-copy">
      <h2>Built for the Coast, Engineered for Excellence</h2>
      <p class="lead">We combine decades of metalwork experience with a deep understanding of North Queensland's unique environmental challenges.</p>
      <div class="features">
        <div class="feat"><div class="feat-icon"><svg width="16" height="16" viewBox="0 0 16 16"><path d="M8 2L3 14M8 2l5 12" fill="none" stroke="#fff" stroke-width="1.6"/></svg></div><h4>Custom Fabrication</h4><p>Every project is custom-measured and built in our workshop to your exact specifications.</p></div>
        <div class="feat"><div class="feat-icon"><svg width="18" height="18" viewBox="0 0 18 18"><circle cx="9" cy="9" r="7" fill="#fff"/><path d="M5.5 9l2.3 2.3L12.5 6.6" fill="none" stroke="#0054AA" stroke-width="1.8"/></svg></div><h4>Premium Materials</h4><p>We only use marine-grade stainless steel and high-tensile aluminum suited for coastal salt air.</p></div>
        <div class="feat"><div class="feat-icon"><svg width="18" height="16" viewBox="0 0 18 16"><circle cx="7" cy="5" r="3" fill="#fff"/><path d="M1 15c0-4 3-6 6-6s6 2 6 6z" fill="#fff"/><path d="M14 2v5M11.5 4.5h5" stroke="#fff" stroke-width="1.5"/></svg></div><h4>Professional Installation</h4><p>Our trade-qualified team ensures every installation is structurally sound and perfectly finished.</p></div>
        <div class="feat"><div class="feat-icon"><svg width="14" height="18" viewBox="0 0 14 18"><path d="M7 1a6 6 0 0 0-6 6c0 4.5 6 10 6 10s6-5.5 6-10a6 6 0 0 0-6-6z" fill="#fff"/><circle cx="7" cy="7" r="2.2" fill="#0054AA"/></svg></div><h4>NQ Specialists</h4><p>Proudly serving Bowen, Airlie Beach, and Townsville with localized expert service.</p></div>
      </div>
    </div>
    <div class="about-media" role="img" aria-label="Welder in protective mask working on a metal frame in the workshop"></div>
    <div class="stat"><strong>25+</strong><span>YEARS EXPERIENCE</span></div>
  </div>
</section>

<section class="recent">
  <div class="wrap">
    <div class="recent-head">
      <div><h2 class="section-title">Recent Installations</h2><p>Explore our portfolio of commercial and residential work across the Whitsundays.</p></div>
      <a class="view-all" href="gallery.html">View Full Gallery <svg width="11" height="10" viewBox="0 0 11 10"><path d="M0 5h9M5 1l4 4-4 4" fill="none" stroke="#0054AA" stroke-width="1.5"/></svg></a>
    </div>
    <div class="gallery">
      <div class="g1" role="img" aria-label="Curved glass balcony balustrade overlooking the bay"></div>
      <div class="g2" role="img" aria-label="Steel and glass staircase in a commercial foyer"></div>
      <div class="g3" role="img" aria-label="Laser-cut decorative driveway gate at a modern home"></div>
    </div>
  </div>
</section>

<section class="reviews">
  <div class="wrap">
    <h2 class="section-title centered">Real Feedback from Local Clients</h2>
    <div class="quotes">
      <blockquote class="quote"><svg width="64" height="44" viewBox="0 0 64 44"><path d="M0 44V24C0 10 8 2 22 0v8c-7 2-10 6-10 12h10v24zM34 44V24C34 10 42 2 56 0v8c-7 2-10 6-10 12h10v24z" fill="#CADEEF"/></svg><p>"The quality of the glass balustrade Brightline installed on our deck is absolutely world-class. It transformed our view and feels incredibly solid."</p><cite>— Liam R., Airlie Beach</cite></blockquote>
      <blockquote class="quote"><svg width="64" height="44" viewBox="0 0 64 44"><path d="M0 44V24C0 10 8 2 22 0v8c-7 2-10 6-10 12h10v24zM34 44V24C34 10 42 2 56 0v8c-7 2-10 6-10 12h10v24z" fill="#CADEEF"/></svg><p>"Professional, on time, and the electric gate works perfectly. The custom design they did for our front fence is the talk of the street."</p><cite>— Jess K., Townsville</cite></blockquote>
      <blockquote class="quote"><svg width="64" height="44" viewBox="0 0 64 44"><path d="M0 44V24C0 10 8 2 22 0v8c-7 2-10 6-10 12h10v24zM34 44V24C34 10 42 2 56 0v8c-7 2-10 6-10 12h10v24z" fill="#CADEEF"/></svg><p>"From the first quote to the final installation, the communication was excellent. They handled the whole process with true NQ craftsmanship."</p><cite>— Owen P., Bowen</cite></blockquote>
    </div>
  </div>
</section>

<section class="contact">
  <div class="wrap">
    <div class="contact-box">
      <div class="contact-copy">
        <h2>Let's Discuss Your Project</h2>
        <p class="lead">Ready to upgrade your home or business? Fill out the form and our team will get back to you within 24 hours for a free site measure and quote.</p>
        <ul class="contact-list">
          <li><span class="ci"><svg width="16" height="16" viewBox="0 0 16 16"><path d="M3 1.5l3 .5 1 3-2 1.2a9 9 0 0 0 4.8 4.8L11 9l3 1 .5 3-1.5 1.5C7 14.5 1.5 9 1.5 3z" fill="none" stroke="#0054AA" stroke-width="1.4"/></svg></span>04XX XXX XXX</li>
          <li><span class="ci"><svg width="16" height="13" viewBox="0 0 16 13"><rect x="1" y="1" width="14" height="11" rx="1" fill="none" stroke="#0054AA" stroke-width="1.4"/><path d="M1 2l7 5 7-5" fill="none" stroke="#0054AA" stroke-width="1.4"/></svg></span>info@brightlinecoatings.com.au</li>
          <li><span class="ci"><svg width="13" height="16" viewBox="0 0 14 18"><path d="M7 1a6 6 0 0 0-6 6c0 4.5 6 10 6 10s6-5.5 6-10a6 6 0 0 0-6-6z" fill="none" stroke="#0054AA" stroke-width="1.5"/><circle cx="7" cy="7" r="2" fill="none" stroke="#0054AA" stroke-width="1.5"/></svg></span>Airlie Beach &amp; Bowen Workshops</li>
        </ul>
      </div>
      <form class="form">
        <div class="row">
          <div class="field"><label>FULL NAME</label><div class="input">John Smith</div></div>
          <div class="field"><label>PHONE NUMBER</label><div class="input">0400 000 000</div></div>
        </div>
        <div class="field"><label>SERVICE REQUIRED</label><div class="input sel">Handrails / Balustrades<svg width="12" height="8" viewBox="0 0 12 8"><path d="M1 1l5 5 5-5" fill="none" stroke="#0054AA" stroke-width="1.4"/></svg></div></div>
        <div class="field"><label>MESSAGE</label><div class="input area">Tell us about your project...</div></div>
        <div class="submit">Send Enquiry</div>
      </form>
    </div>
  </div>
</section>

<footer class="footer">
  <div class="wrap footer-cols">
    <div class="fcol"><div class="f-brand">Brightline Coatings Co</div><p class="f-tag">Precision Craftsmanship for the Coast. Your local partners in architectural metal and glass.</p></div>
    <div class="fcol"><h5>SERVICES</h5><ul><li><a href="handrails.html">Handrails</a></li><li><a href="privacy-screens.html">Privacy Screens</a></li><li><a href="electric-gates.html">Electric Gates</a></li><li><a href="pool-fencing.html">Pool Fencing</a></li><li><a href="glass-balustrades.html">Glass Balustrades</a></li></ul></div>
    <div class="fcol"><h5>AREAS SERVED</h5><ul><li>Airlie Beach</li><li>Bowen</li><li>Cannonvale</li><li>Proserpine</li><li>Townsville</li></ul></div>
    <div class="fcol"><h5>CONTACT</h5><p class="f-contact">Available Mon-Fri 7:00 AM - 5:00 PM</p><a class="f-btn" href="contact.html">Request Quote</a></div>
  </div>
  <div class="footer-bottom"><span>© 2024 Brightline Coatings Co. Precision Craftsmanship for the Coast.</span><nav><a href="privacy.html">Privacy Policy</a><a href="terms.html">Terms of Service</a></nav></div>
</footer>

</body>
</html>
```